Design Website Templates for Photographers for Lumera Inc. (trylumera.example)

Lumera Inc. is a generative website company for wedding photographers.
We are seeking new photography website design inspirations for the next template to be offered on our platform. The catch is you must use the same data for your designs. You also must use all of the data somewhere in the design. You cannot add new content besides the data available. If you wish to add any elements It will be hardcoded and must be universally fitting for many different photographers. We recommend not using any hardcoded test.
Don't be afraid to be creative! Although the most important element of a photographers website is the photos, we are looking for unique and out-of-the-box designs for the actual site as well.
Here is the User generated data available to you:
- 4 Hero Images Landscape, 4 Hero Images Portrait
- Tagline “destination photographer based in Maui, Hawaii”
- “About Photo” of the photographer
- “About” Biography Text
- The design can use up to 3 colors + background color and 2 fonts
- 9 Gallery images
- 3 Packages/services that include landscape/portrait images, a price, a title and text
- Testimonials made up of an image, text and text for the name of testimonial giver
See some examples of our current website designs attached. You can use any of the data you see in the designs.
Updates
We are looking for designs that are less feminine and are more neutral in color and fonts. Currently our templates are more oriented towards feminine photographers. We want to have designs that speak to diverse audiences. We thank everyone for submitting and are reviewing the designs.
Number of Pages Required
1 page
Look and feel
Each slider illustrates characteristics of the customer's brand and the style your logo design should communicate.

```html
<!DOCTYPE html>
<html lang="en">
<head>
<meta charset="utf-8">
<title>Nia Calder — Destination Photographer</title>
<link href="https://fonts.googleapis.com/css2?family=Bodoni+Moda:wght@400&family=Poppins:ital,wght@0,400;0,500;0,600;0,700;1,400&display=swap" rel="stylesheet">
<style>
:root{
  --bg:#f2f8f8;
  --teal:#1f8b94;
  --teal-soft:#cfe6e6;
  --amber:#f9a602;
  --ink:#2f3b3d;
  --night:#1d3533;
  --white:#ffffff;
  --serif:'Bodoni Moda', serif;
  --sans:'Poppins', sans-serif;
}
*{box-sizing:border-box;margin:0;padding:0}
html,body{width:1200px;height:3997px;overflow:hidden}
body{background:var(--bg);font-family:var(--sans);color:var(--ink);position:relative}
.abs{position:absolute}
.section-title{position:absolute;left:0;width:1200px;text-align:center;font-family:var(--serif);font-weight:400;color:var(--teal);font-size:34px;letter-spacing:10px;text-transform:uppercase}

/* hero */
.hero{position:absolute;left:0;top:0;width:1200px;height:620px;background:linear-gradient(160deg,#4a4b45 0%,#7b7a70 30%,#8c8f8a 50%,#5b5a50 72%,#2f2d27 100%)}
.hero-wave{position:absolute;left:0;top:0}
.logo{position:absolute;font-family:var(--sans);font-weight:600;color:var(--white);font-size:29px;letter-spacing:1px;text-transform:uppercase}
.main-nav{position:absolute;left:456px;top:26px;display:flex;gap:22px}
.main-nav a{color:var(--white);font-size:11px;letter-spacing:.5px;text-decoration:none;text-transform:uppercase}
.btn-book{position:absolute;left:864px;top:22px;width:105px;height:24px;border-radius:12px;background:var(--amber);color:var(--white);font-size:11px;text-align:center;line-height:24px;text-transform:uppercase;letter-spacing:.5px}
.tagline{position:absolute;left:0;top:372px;width:1200px;text-align:center;font-family:var(--serif);color:var(--white);font-size:29px;letter-spacing:5px;line-height:34px;text-transform:uppercase;text-shadow:0 2px 6px rgba(0,0,0,.35)}
.slide-dots{position:absolute;left:554px;top:458px;display:flex;gap:13px}
.slide-dots span{width:13px;height:13px;border-radius:50%;background:#555}
.slide-dots span.on{background:var(--teal)}

/* welcome */
.welcome-text{position:absolute;left:331px;top:683px;width:270px;font-size:13px;line-height:23px;color:var(--ink)}
.welcome-text p{margin-bottom:22px}
.rule{position:absolute;height:1px;background:#bcd5d5}
.follow{position:absolute;left:331px;top:974px;font-size:12.5px;letter-spacing:1px}
.social{position:absolute;width:28px;height:28px;border:1.5px solid var(--teal);border-radius:50%}
.arch{position:absolute;border:1.5px solid var(--teal-soft);border-radius:999px;padding:10px}
.arch .fill{width:100%;height:100%;border-radius:999px}

/* gallery */
.gallery-frame{position:absolute;left:217px;top:1192px;width:764px;height:547px;border:1.5px solid var(--teal-soft)}
.shot{position:absolute}
.view-more{position:absolute;left:0;top:1753px;width:1200px;text-align:center;color:var(--amber);font-weight:700;font-size:17px;letter-spacing:5px}

/* packages */
.package{position:absolute;top:1952px;width:235px;height:358px;border:1.5px solid var(--teal-soft);border-radius:999px;padding:10px}
.package .fill{position:relative;width:100%;height:100%;border-radius:999px;overflow:hidden}
.package-info{position:absolute;left:0;top:196px;width:100%;text-align:center;color:var(--white)}
.package-title{font-weight:700;font-size:13px;letter-spacing:1.5px;line-height:26px;text-transform:uppercase}
.package-desc{font-size:11px;margin-top:4px}
.package-price{display:inline-block;color:var(--amber);font-size:15px;margin-top:4px;border-bottom:1px solid var(--amber);line-height:20px}

/* testimonials */
.testimonials-band{position:absolute;left:0;top:2424px;width:1200px;height:510px;background:linear-gradient(180deg,#e9e9e7 0%,#e2e1dc 45%,#b9a98a 68%,#9c8a68 100%)}
.quote-card{position:absolute;top:2533px;width:229px;height:362px;background:var(--white);border-radius:999px;text-align:center}
.quote-mark{margin-top:22px;font-family:var(--serif);font-size:70px;line-height:60px;color:#c9dcdc}
.quote-text{margin:14px auto 0;width:190px;font-style:italic;font-size:11.5px;line-height:22.5px;color:#4c5556}
.quote-rule{position:absolute;left:58px;top:284px;width:113px;height:1px;background:#bcd5d5}
.quote-name{position:absolute;left:0;top:293px;width:100%;font-weight:600;font-size:14px;color:var(--teal)}

/* contact */
.field{position:absolute;left:380px;width:440px;height:30px;border-bottom:1px solid #cfe0e0;padding-left:12px;font-size:13px;letter-spacing:1px;color:var(--ink)}
.btn-send{position:absolute;left:382px;top:3306px;width:135px;height:31px;border-radius:16px;background:var(--amber);color:var(--white);font-weight:600;font-size:12px;letter-spacing:1.5px;text-align:center;line-height:31px}

/* instagram strip */
.insta-strip{position:absolute;left:0;top:3427px;width:750px;height:137px;border-radius:0 70px 70px 0;overflow:hidden;display:flex;box-shadow:6px 6px 12px rgba(0,0,0,.18)}
.insta-strip div{height:100%}
.handle{position:absolute;left:756px;top:3478px;width:165px;height:33px;border:1.5px solid var(--teal);border-radius:17px;font-size:12.5px;line-height:30px;padding-left:50px;color:var(--ink)}
.handle .dot{position:absolute;left:7px;top:5px;width:20px;height:20px;border:1.5px solid var(--teal);border-radius:50%}

/* footer */
.footer-links{position:absolute;top:3806px;color:var(--white);font-size:14px;letter-spacing:3px;text-transform:uppercase}
.footer-sub{position:absolute;color:#8fa6a3;font-size:11px;line-height:22px}
.btn-outline{position:absolute;left:231px;top:3800px;width:171px;height:31px;border:1.5px solid var(--amber);border-radius:16px;color:var(--amber);font-size:14px;letter-spacing:2px;text-align:center;line-height:28px}
</style>
</head>
<body>

<header class="hero" role="img" aria-label="Hero photo: couple embracing on a rocky seashore under a cloudy sky"></header>
<svg class="hero-wave" width="1200" height="620" viewBox="0 0 1200 620" aria-hidden="true">
  <path d="M0,553 C230,488 450,495 660,540 C860,585 1040,622 1200,560 L1200,620 L0,620 Z" fill="var(--bg)"/>
  <polyline points="232,242 204,267 232,292" fill="none" stroke="#fff" stroke-width="1.5"/>
  <polyline points="968,242 996,267 968,292" fill="none" stroke="#fff" stroke-width="1.5"/>
</svg>
<div class="logo" style="left:225px;top:13px">Nia Calder</div>
<nav class="main-nav"><a>About</a><a>Blog</a><a>Portfolio</a><a>Testimonials</a><a>Get in touch</a></nav>
<div class="btn-book">Book now</div>
<h1 class="tagline">Destination photographer<br>based in Maui, Hawaii</h1>
<div class="slide-dots"><span class="on"></span><span></span></div>

<h2 class="section-title" style="text-align:left;left:331px;width:auto;top:622px">Welcome</h2>
<div class="welcome-text">
  <p>Nice to meet you, I'm Nia Calder, a Maui, Hawaii based destination wedding photographer.</p>
  <p>Here's some information about me, sed do eiusmod tempor incididunt ut labore et dolore magna aliqua.</p>
  <p>Quis ipsum suspendisse ultrices gravida. Risus commodo viverra maecenas accumsan lacus velis.</p>
</div>
<div class="rule" style="left:331px;top:951px;width:230px"></div>
<div class="follow">Follow Me</div>
<div class="social" style="left:330px;top:1007px"></div>
<div class="social" style="left:370px;top:1007px"></div>
<div class="social" style="left:410px;top:1007px"></div>
<div class="arch" style="left:646px;top:667px;width:235px;height:357px">
  <div class="fill" role="img" aria-label="Portrait of the photographer holding a camera" style="background:linear-gradient(180deg,#e9e6e0,#9c958c 55%,#2a2a2c)"></div>
</div>

<h2 class="section-title" style="top:1138px">Recent Works</h2>
<div class="gallery-frame"></div>
<div class="shot" role="img" aria-label="Bride with bridesmaids" style="left:230px;top:1203px;width:229px;height:127px;background:linear-gradient(135deg,#d9cfc6,#8f6f66)"></div>
<div class="shot" role="img" aria-label="Couple beneath a clear umbrella in the rain" style="left:478px;top:1203px;width:244px;height:251px;background:linear-gradient(160deg,#9fb6d2,#5e6f95 55%,#8a5a3a)"></div>
<div class="shot" role="img" aria-label="Couple walking among palm trees" style="left:742px;top:1203px;width:226px;height:127px;background:linear-gradient(180deg,#f4f1e6,#c9c29b 60%,#7d7a45)"></div>
<div class="shot" role="img" aria-label="Couple standing on a beach" style="left:230px;top:1346px;width:229px;height:237px;background:linear-gradient(180deg,#f7f1e8,#e6dccb 60%,#c8b79c)"></div>
<div class="shot" role="img" aria-label="Bride on stone steps with mountain view" style="left:742px;top:1346px;width:226px;height:237px;background:linear-gradient(170deg,#b4c2d0,#7f8e8c 45%,#ddd7d0)"></div>
<div class="shot" role="img" aria-label="Couple kissing in a garden" style="left:478px;top:1471px;width:244px;height:256px;background:linear-gradient(150deg,#b9cfa4,#7c8fa8 55%,#d7cdc2)"></div>
<div class="shot" role="img" aria-label="Couple at sunset in a field" style="left:230px;top:1599px;width:229px;height:128px;background:linear-gradient(180deg,#e6ad5e,#a06428 55%,#4a2e17)"></div>
<div class="shot" role="img" aria-label="Couple walking through golden grass" style="left:742px;top:1599px;width:226px;height:128px;background:linear-gradient(180deg,#c99a66,#a86a38 55%,#5d3a1c)"></div>
<div class="view-more">VIEW MORE &#8250;</div>

<h2 class="section-title" style="top:1880px">Featured Packages</h2>
<div class="package" style="left:220px">
  <div class="fill" role="img" aria-label="Couple with a horse in the woods" style="background:linear-gradient(180deg,#56604e,#6c6a5f 50%,#4c4a44)">
    <div class="package-info"><div class="package-title">Wedding collection<br>one</div><div class="package-desc">A brief description text here</div><div class="package-price">$1300</div></div>
  </div>
</div>
<div class="package" style="left:483px">
  <div class="fill" role="img" aria-label="Couple embracing on the beach" style="background:linear-gradient(180deg,#6e6b66,#88837b 50%,#6d665e)">
    <div class="package-info"><div class="package-title">Wedding collection<br>two</div><div class="package-desc">A brief description text here</div><div class="package-price">$1500</div></div>
  </div>
</div>
<div class="package" style="left:745px">
  <div class="fill" role="img" aria-label="Couple sharing a close moment" style="background:linear-gradient(180deg,#5d5047,#7a6b60 50%,#5a4d44)">
    <div class="package-info"><div class="package-title">Wedding collection<br>three</div><div class="package-desc">A brief description text here</div><div class="package-price">$2000</div></div>
  </div>
</div>

<div class="testimonials-band" role="img" aria-label="Background photo of a couple in a grassy field with a house and palm trees"></div>
<h2 class="section-title" style="top:2465px">Client Testimonials</h2>
<div class="quote-card" style="left:230px">
  <div class="quote-mark">&ldquo;</div>
  <p class="quote-text">Lorem ipsum dolor sit amet, con sectetur adipiscing elit, sed do eiusmod tempor in cidi dunt ut labore et dolore magna aliqua. Quis ipsum suspen disse ultrices gravida. Risus commodo viverra mae cenas accumsan lacus velis.</p>
  <div class="quote-rule"></div><div class="quote-name">Ava &amp; Leo</div>
</div>
<div class="quote-card" style="left:486px">
  <div class="quote-mark">&ldquo;</div>
  <p class="quote-text">Sed do eiusmod tempor in cidi dunt ut labore et dolore magna aliqua. Quis ipsum suspen disse ultrices gravida. Risus commodo viverra mae cenas accumsan lacus velis.</p>
  <div class="quote-rule"></div><div class="quote-name">Iris &amp; Sam</div>
</div>
<div class="quote-card" style="left:740px">
  <div class="quote-mark">&ldquo;</div>
  <p class="quote-text">Dolor sit amet, con sec tetur adi piscing elit, sed do eiu smod tempor in cidi dunt ut labore et dolore magna aliqua. Quis ipsum suspen disse ultrices gravida. Risus commodo viverra mae cenas accumsan lacus velis.</p>
  <div class="quote-rule"></div><div class="quote-name">June &amp; Oscar</div>
</div>

<h2 class="section-title" style="top:3013px">Get in Touch</h2>
<div class="field" style="top:3100px">Full Name *</div>
<div class="field" style="top:3150px">Email Address *</div>
<div class="field" style="top:3200px">Phone Number *</div>
<div class="field" style="top:3251px">Your Message *</div>
<div class="btn-send">SEND</div>

<div class="insta-strip">
  <div role="img" aria-label="Couple near a city landmark" style="width:144px;background:linear-gradient(180deg,#d9d9d9,#6f6f6f)"></div>
  <div role="img" aria-label="Couple celebrating at dusk" style="width:183px;background:linear-gradient(180deg,#6b5a45,#3a2f24)"></div>
  <div role="img" aria-label="Couple under a flowing veil" style="width:167px;background:linear-gradient(180deg,#ecdcc9,#b98d68)"></div>
  <div role="img" aria-label="Couple walking in a golden field" style="width:139px;background:linear-gradient(180deg,#c99a66,#6e4622)"></div>
  <div role="img" aria-label="Couple kissing in warm light" style="width:117px;background:linear-gradient(180deg,#5a3d2a,#1f1712)"></div>
</div>
<div class="handle"><span class="dot"></span>@niacalder</div>

<svg class="abs" style="left:0;top:3540px" width="1200" height="457" viewBox="0 0 1200 457" aria-hidden="true">
  <path d="M0,72 C260,150 620,20 1200,25 L1200,457 L0,457 Z" fill="var(--night)"/>
</svg>
<div class="logo" style="left:0;width:1200px;text-align:center;top:3712px;font-size:27px">Nia Calder</div>
<div class="rule" style="left:354px;top:3769px;width:496px;background:#3c5553"></div>
<div class="btn-outline">BOOK NOW</div>
<div class="footer-links" style="left:444px">About</div>
<div class="footer-sub" style="left:444px;top:3830px">- Meet Me<br>- Our Team</div>
<div class="footer-links" style="left:554px">Blog</div>
<div class="footer-links" style="left:652px">Testimonials</div>
<div class="footer-links" style="left:829px">Portfolio</div>
<div class="footer-sub" style="left:833px;top:3827px">- Photography<br>- Filmography</div>

</body>
</html>
```